E-learning Information & Community Website Needs a Makeover

I'm looking for a design makeover for my website "Tavipor.club". Tavipor's aim is to connect people to online learning through forums, information, guides & independent reviews. The site was launched in September 2014 using a forum software (Xenforo), but now needs a more polished and sophisticated look which communicates expertise and professionalism. I would like to see designs that use the current "Tavipor" blue (#0070c0). To visit the current website, go to http://www.tavipor.club/

Target Market(s)

People wishing to study online

Industry/Entity Type

Club

Number of Pages Required

4 page

Font styles to use
Sans Serif

Requirements
Must have
• A simple, clear and sophisticated lading page with links to the site's key features: discussion forums, Useful resources, Reviews, News etc, Articles. (See layout idea file attached)
• The main pages are the Landing Page, Discussion Forums, Resources & Reviews
• I would like to see designs that use the current "Tavipor" blue (#0070c0).
Nice to have
• Something uncluttered and easy to understand. The design should convey expertise in the field of online learning, giving users a sense of trust in the site's offerings.
• To give an idea of the sort of thing I'm after, take a look at wendricast.com website (screenshot attached)

```html
<!DOCTYPE html>
<html lang="en">
<head>
<meta charset="utf-8">
<title>Tavipor – Connecting people to online learning</title>
<link rel="stylesheet" href="https://fonts.googleapis.com/css2?family=Cabin:ital,wght@0,400;0,500;0,600;1,400&display=swap">
<style>
:root{
  --brand:#0070c0;
  --hero-top:#1d86dc;
  --hero-bottom:#0d64bd;
  --sky:#7ccaf2;
  --header:#2e2e2e;
  --green:#8cc63f;
  --green-dark:#6aa82a;
  --ink:#555;
  --line:#d9d9d9;
  --band:#ececec;
  --footer:#e5f2f2;
  --tile-green:#8dc63f;
  --tile-orange:#f47b50;
  --tile-purple:#7e72b0;
  --tile-red:#e1506b;
  --tile-blue:#5bbde0;
  --tile-yellow:#f5c842;
  --white:#fff;
}
*{box-sizing:border-box;margin:0;padding:0}
html,body{width:1027px;height:1200px;overflow:hidden;background:var(--white)}
body{position:relative;font-family:"Cabin",Arial,sans-serif;color:var(--ink)}
.abs{position:absolute}
a{color:inherit;text-decoration:none}

/* header */
.site-header{left:0;top:0;width:1027px;height:47px;background:var(--header)}
.site-logo{left:138px;top:8px;font-size:25px;color:#a9d8f5;font-weight:400}
.main-nav{left:276px;top:15px;display:flex;font-size:12.5px;color:var(--white)}
.main-nav a{margin-right:16px}
.login{left:801px;top:15px;font-size:12.5px;color:#8fcaf2}
.divider{left:836px;top:14px;color:#aaa;font-size:13px}
.signup{left:846px;top:11px;width:53px;height:24px;border-radius:4px;background:var(--brand);color:#fff;font-size:12.5px;text-align:center;line-height:24px}

/* hero */
.hero{left:0;top:47px;width:1027px;height:381px;background:linear-gradient(180deg,var(--hero-top),var(--hero-bottom))}
.hero-kicker{left:137px;top:133px;font-size:26px;color:var(--sky)}
.hero-title{left:137px;top:160px;font-size:46px;line-height:51px;color:var(--white);font-weight:500}
.btn-green{background:linear-gradient(180deg,#a6d94f,var(--green-dark));color:#fff;border-radius:17px;text-align:center}
.hero-cta{left:136px;top:280px;width:187px;height:34px;line-height:34px;font-size:17px}
.hero-art{left:510px;top:100px;width:445px;height:292px;border-radius:20px;background:radial-gradient(circle at 55% 45%,rgba(255,255,255,.35),rgba(255,255,255,.08) 70%)}
.share-dots{left:832px;top:75px;display:flex;gap:3px}
.share-dots span{width:12px;height:12px;border-radius:50%;background:rgba(255,255,255,.85)}

/* feature tiles */
.tile{top:405px;width:85px;height:85px}
.tile svg{position:absolute;left:22px;top:22px}
.tile-label{top:498px;width:110px;text-align:center;font-size:12px;color:#666}

/* share panel */
.share-title{left:752px;top:433px;font-size:10px;font-style:italic;color:var(--brand)}
.share-btn{height:12px;font-size:7px;line-height:11px;padding:0 4px;border:1px solid #c9c9c9;background:#f3f3f3;color:#333;border-radius:2px}
.share-btn.dark{background:#3b5b98;color:#fff;border-color:#3b5b98}
.share-btn.mid{background:var(--brand);color:#fff;border-color:var(--brand)}
.count{height:12px;font-size:7px;line-height:10px;padding:0 3px;border:1px solid #c9c9c9;background:#fff;color:#555}

/* partner band */
.partner-band{left:0;top:540px;width:1027px;height:104px;background:var(--band)}
.partner-box{left:136px;top:560px;width:761px;height:65px;background:var(--white);box-shadow:0 1px 2px rgba(0,0,0,.1)}
.partner{top:583px;font-size:15px;color:#8f8f8f;font-weight:600;display:flex;align-items:center;gap:5px}
.partner i{display:inline-block;width:16px;height:16px;background:#b5b5b5;border-radius:50%}
.arrow{top:582px;color:#c9c9c9;font-size:20px}

/* threads */
.threads-head{top:656px;font-size:13px;color:var(--brand)}
.threads-title{left:141px}
.threads-rule{left:139px;width:552px;height:1px;background:var(--line)}
.avatar{width:52px;height:52px;border-radius:50%;background:var(--brand);color:#fff;font-size:9px;text-align:center;padding-top:13px;line-height:11px}
.ribbon{height:11px;font-size:8px;line-height:11px;color:#fff;padding:0 5px}
.thread-title{font-size:12px;color:var(--brand)}
.thread-meta{font-size:9.5px;color:#888}
.reply-box{width:41px;height:29px;background:var(--brand);color:#fff;font-size:12px;text-align:center;line-height:29px}
.last-msg{font-size:9px;line-height:11px;color:#888}
.last-msg b{color:var(--brand);font-weight:400}

/* sidebar */
.feed-box{left:708px;top:651px;width:188px;height:199px;background:#e5f1f5}
.feed-head{left:747px;top:666px;font-size:12px;color:var(--brand)}
.feed-bird{left:718px;top:661px;width:24px;height:24px;border-radius:50%;background:var(--brand)}
.feed-list{left:714px;top:693px;width:177px;height:148px;background:#fff}
.feed-item{font-size:7.5px;line-height:9px;color:#333}
.feed-item b{font-size:8px}
.feed-item em{font-style:normal;color:var(--brand)}
.feed-thumb{left:718px;width:26px;height:26px;background:#dfe7ee}
.follow-box{left:708px;top:860px;width:188px;height:91px;background:#efefef}
.follow-head{left:720px;top:871px;font-size:12.5px;color:var(--brand)}
.follow-icon{top:895px;width:29px;height:29px;border-radius:3px}

/* more */
.more{left:445px;top:985px;width:147px;height:46px;border-radius:74px 74px 0 0;background:var(--brand);color:#fff;font-size:11px;text-align:center;padding-top:7px}

/* footer */
.site-footer{left:0;top:1008px;width:1027px;height:192px;background:var(--footer)}
.footer-tag{left:0;top:1033px;width:1027px;text-align:center;font-size:19.5px;font-style:italic;color:var(--brand)}
.footer-cta{left:423px;top:1064px;width:187px;height:34px;line-height:34px;font-size:17px}
.footer-links{left:249px;top:1110px;width:532px;height:47px;background:#f7fbfb;font-size:11px;color:var(--brand)}
.footer-links span{position:absolute;top:16px}
.copy{left:282px;top:1172px;font-size:8px;color:#777}
.legal{top:1172px;font-size:8px;color:var(--brand)}
.foot-dots{left:528px;top:1172px;display:flex;gap:3px}
.foot-dots span{width:12px;height:12px;border-radius:50%;background:#2f6fa8}
</style>
</head>
<body>

<header class="abs site-header">
  <div class="abs site-logo">Tavipor</div>
  <nav class="abs main-nav">
    <a>Home</a><a>Forums</a><a>Resources</a><a>Members</a><a>FAQ</a><a>Blog</a><a>Tavipor Español</a><a>Course Scoop</a>
  </nav>
  <a class="abs login">Login</a><span class="abs divider">|</span>
  <a class="abs signup">Signup</a>
</header>

<section class="abs hero"></section>
<div class="abs share-dots"><span></span><span></span><span></span><span></span></div>
<div class="abs hero-kicker">At the heart of</div>
<h1 class="abs hero-title">connecting people to<br>online learning</h1>
<a class="abs btn-green hero-cta">Sign Up For Free</a>
<div class="abs hero-art" role="img" aria-label="Illustration of a computer screen showing the Tavipor name, surrounded by a classroom, graduation cap, gear, phone, laptop and signpost joined by a dashed circle"></div>

<!-- feature tiles -->
<div class="abs tile" style="left:136px;background:var(--tile-green)">
  <svg width="41" height="41" viewBox="0 0 41 41"><circle cx="20.5" cy="20.5" r="18" fill="none" stroke="#fff" stroke-width="3"/><path d="M16 12 L29 20.5 L16 29Z" fill="#fff"/></svg>
</div>
<div class="abs tile" style="left:238px;background:var(--tile-orange)">
  <svg width="41" height="41" viewBox="0 0 41 41"><path d="M3 5h35v24H16l-8 7v-7H3z" fill="#fff"/><path d="M9 12h23M9 17h23M9 22h18" stroke="var(--tile-orange)" stroke-width="2"/></svg>
</div>
<div class="abs tile" style="left:341px;background:var(--tile-purple)">
  <svg width="41" height="41" viewBox="0 0 41 41"><rect x="3" y="4" width="35" height="27" rx="7" fill="#fff"/><path d="M12 31l-3 7 9-7z" fill="#fff"/><circle cx="20.5" cy="17.5" r="9" fill="var(--tile-purple)"/><path d="M16 17.5l3.5 3.5 6-6.5" stroke="#fff" stroke-width="2.5" fill="none"/></svg>
</div>
<div class="abs tile" style="left:444px;background:var(--tile-red)">
  <svg width="41" height="41" viewBox="0 0 41 41"><path d="M20.5 3a11 11 0 0 0-6 20v5h12v-5a11 11 0 0 0-6-20z" fill="none" stroke="#fff" stroke-width="2.5"/><path d="M15 32h11M16.5 36h8" stroke="#fff" stroke-width="2.5"/></svg>
</div>
<div class="abs tile" style="left:546px;background:var(--tile-blue)">
  <svg width="41" height="41" viewBox="0 0 41 41"><path d="M8 2h18l8 8v29H8z" fill="#fff"/><path d="M13 16h16M13 21h16M13 26h16M13 31h12" stroke="var(--tile-blue)" stroke-width="1.5"/></svg>
</div>
<div class="abs tile" style="left:650px;background:var(--tile-yellow)">
  <svg width="41" height="41" viewBox="0 0 41 41"><rect x="2" y="9" width="37" height="24" fill="#fff"/><path d="M2 9l18.5 14L39 9" stroke="var(--tile-yellow)" stroke-width="2" fill="none"/></svg>
</div>
<div class="abs tile-label" style="left:123px">Getting Started</div>
<div class="abs tile-label" style="left:225px">Discussions</div>
<div class="abs tile-label" style="left:327px">Reviews</div>
<div class="abs tile-label" style="left:431px">Tips &amp; Guidelines</div>
<div class="abs tile-label" style="left:533px">News &amp; Articles</div>
<div class="abs tile-label" style="left:637px">Newsletter</div>

<!-- share panel -->
<div class="abs share-title">Share This Page</div>
<div class="abs share-btn" style="left:751px;top:455px">Post</div>
<div class="abs count" style="left:789px;top:455px">139</div>
<div class="abs share-btn" style="left:834px;top:455px">+1</div>
<div class="abs count" style="left:857px;top:455px">21</div>
<div class="abs share-btn dark" style="left:751px;top:472px">Recommend</div>
<div class="abs count" style="left:808px;top:472px">157</div>
<div class="abs share-btn mid" style="left:834px;top:473px">Share</div>
<div class="abs count" style="left:876px;top:473px">43</div>

<!-- partner band -->
<section class="abs partner-band"></section>
<div class="abs partner-box"></div>
<div class="abs arrow" style="left:140px">‹</div>
<div class="abs arrow" style="left:880px">›</div>
<div class="abs partner" style="left:205px"><i></i>Paylumen</div>
<div class="abs partner" style="left:345px"><i></i>Korvane</div>
<div class="abs partner" style="left:455px"><i></i>Nillo</div>
<div class="abs partner" style="left:520px">Shopwick</div>
<div class="abs partner" style="left:610px"><i></i>Pagestead</div>
<div class="abs partner" style="left:728px"><i></i>Ravelstock</div>

<!-- recent threads -->
<div class="abs threads-head threads-title">Recent Threads</div>
<div class="abs threads-head" style="left:470px;top:657px;font-size:12px">Replies</div>
<div class="abs threads-head" style="left:534px;top:657px;font-size:12px">Views</div>
<div class="abs threads-head" style="left:607px;top:657px;font-size:12px">Last Message</div>
<div class="abs threads-rule" style="top:679px"></div>

<div class="abs avatar" style="left:139px;top:686px">Tavipor<br>Lab</div>
<div class="abs ribbon" style="left:148px;top:725px;background:var(--green)">Advice</div>
<div class="abs thread-title" style="left:209px;top:696px">How many MOOCs have you done?</div>
<div class="abs thread-meta" style="left:209px;top:714px">Marisol, Sep 19, 2014, MOOC Discussions</div>
<div class="abs reply-box" style="left:469px;top:689px">01</div>
<svg class="abs" style="left:528px;top:691px" width="42" height="26" viewBox="0 0 42 26"><path d="M1 13C11 1 31 1 41 13 31 25 11 25 1 13z" fill="var(--brand)"/><circle cx="21" cy="13" r="9" fill="#fff"/><circle cx="21" cy="13" r="7.5" fill="var(--brand)"/><text x="21" y="17" fill="#fff" font-size="10" text-anchor="middle" font-family="Cabin,sans-serif">36</text></svg>
<div class="abs last-msg" style="left:606px;top:692px"><b>Marisol,</b><br>Yesterday at 4:41 PM</div>
<div class="abs threads-rule" style="top:751px"></div>

<div class="abs avatar" style="left:139px;top:757px">Tavipor<br>Lab</div>
<div class="abs ribbon" style="left:148px;top:795px;background:var(--green)">Advice</div>
<div class="abs thread-title" style="left:209px;top:767px">How many MOOCs have you done?</div>
<div class="abs thread-meta" style="left:209px;top:785px">Marisol, Sep 19, 2014, MOOC Discussions</div>
<div class="abs reply-box" style="left:469px;top:761px">01</div>
<svg class="abs" style="left:528px;top:762px" width="42" height="26" viewBox="0 0 42 26"><path d="M1 13C11 1 31 1 41 13 31 25 11 25 1 13z" fill="var(--brand)"/><circle cx="21" cy="13" r="9" fill="#fff"/><circle cx="21" cy="13" r="7.5" fill="var(--brand)"/><text x="21" y="17" fill="#fff" font-size="10" text-anchor="middle" font-family="Cabin,sans-serif">36</text></svg>
<div class="abs last-msg" style="left:606px;top:763px"><b>Marisol,</b><br>Yesterday at 4:41 PM</div>
<div class="abs threads-rule" style="top:822px"></div>

<div class="abs avatar" style="left:139px;top:830px">Tavipor<br>Lab</div>
<div class="abs ribbon" style="left:148px;top:869px;background:var(--tile-orange)">Courses</div>
<div class="abs thread-title" style="left:209px;top:841px">How many MOOCs have you done?</div>
<div class="abs thread-meta" style="left:209px;top:859px">Marisol, Sep 19, 2014, MOOC Discussions</div>
<div class="abs reply-box" style="left:469px;top:835px">01</div>
<svg class="abs" style="left:528px;top:836px" width="42" height="26" viewBox="0 0 42 26"><path d="M1 13C11 1 31 1 41 13 31 25 11 25 1 13z" fill="var(--brand)"/><circle cx="21" cy="13" r="9" fill="#fff"/><circle cx="21" cy="13" r="7.5" fill="var(--brand)"/><text x="21" y="17" fill="#fff" font-size="10" text-anchor="middle" font-family="Cabin,sans-serif">36</text></svg>
<div class="abs last-msg" style="left:606px;top:837px"><b>Marisol,</b><br>Yesterday at 4:41 PM</div>
<div class="abs threads-rule" style="top:895px"></div>

<div class="abs avatar" style="left:139px;top:907px">Tavipor<br>Lab</div>
<div class="abs ribbon" style="left:148px;top:946px;background:var(--green)">Advice</div>
<div class="abs thread-title" style="left:209px;top:918px">How many MOOCs have you done?</div>
<div class="abs thread-meta" style="left:209px;top:936px">Marisol, Sep 19, 2014, MOOC Discussions</div>
<div class="abs reply-box" style="left:469px;top:912px">01</div>
<svg class="abs" style="left:528px;top:913px" width="42" height="26" viewBox="0 0 42 26"><path d="M1 13C11 1 31 1 41 13 31 25 11 25 1 13z" fill="var(--brand)"/><circle cx="21" cy="13" r="9" fill="#fff"/><circle cx="21" cy="13" r="7.5" fill="var(--brand)"/><text x="21" y="17" fill="#fff" font-size="10" text-anchor="middle" font-family="Cabin,sans-serif">36</text></svg>
<div class="abs last-msg" style="left:606px;top:914px"><b>Marisol,</b><br>Yesterday at 4:41 PM</div>

<!-- sidebar -->
<aside>
  <div class="abs feed-box"></div>
  <div class="abs feed-bird"></div>
  <div class="abs feed-head">Chirpline Feeds</div>
  <div class="abs feed-list"></div>
  <div class="abs feed-thumb" style="top:698px"></div>
  <div class="abs feed-item" style="left:749px;top:697px;width:136px"><b>Nimbusforge</b> <span style="color:#999">@Nimbusforge</span><br>@dariusvell is back with a blogpost on #API Interactions with #KVO in #ObjectiveC! - <em>shrt.vx/1f72tgM</em><br><span style="color:#999">Promoted by Nimbusforge</span></div>
  <div class="abs threads-rule" style="left:714px;width:177px;top:756px"></div>
  <div class="abs feed-thumb" style="top:762px"></div>
  <div class="abs feed-item" style="left:749px;top:761px;width:136px"><b>Civic Ledger</b> <span style="color:#999">@CivicLedger</span><br>Here's why shady for-profit colleges don't get shut down <em>cvl.vx/1erVP8Q</em></div>
  <div class="abs threads-rule" style="left:714px;width:177px;top:798px"></div>
  <div class="abs feed-thumb" style="top:803px"></div>
  <div class="abs feed-item" style="left:749px;top:802px;width:136px"><b>Tradewire Tech</b> <span style="color:#999">@TWT</span><br>New Yorkers may be more superficial than people in LA when it comes to dating <em>twr.vx/1fbP7CP</em></div>

  <div class="abs follow-box"></div>
  <div class="abs follow-head">FOLLOW US</div>
  <div class="abs follow-icon" style="left:721px;background:#3b5b98"></div>
  <div class="abs follow-icon" style="left:753px;background:#2fa8e0"></div>
  <div class="abs follow-icon" style="left:785px;background:#d9d9d9"></div>
  <div class="abs follow-icon" style="left:816px;background:#111"></div>
  <div class="abs follow-icon" style="left:848px;background:#27a9d8"></div>
</aside>

<a class="abs more">⌄ more activities</a>

<footer class="abs site-footer"></footer>
<div class="abs footer-tag">At the heart of connecting people to online learning</div>
<a class="abs btn-green footer-cta">Sign Up For Free</a>
<nav class="abs footer-links">
  <span style="left:35px">About</span>
  <span style="left:78px">Contact Us</span>
  <span style="left:145px">Help</span>
  <span style="left:181px">Home</span>
  <span style="left:224px">FAQ</span>
  <span style="left:258px">Community Guidelines</span>
  <svg class="abs" style="left:475px;top:15px" width="16" height="16" viewBox="0 0 16 16"><circle cx="8" cy="8" r="8" fill="var(--brand)"/><path d="M4.5 10l3.5-3.5 3.5 3.5" stroke="#fff" stroke-width="2" fill="none"/></svg>
  <span style="left:496px;color:#555;font-size:10px">Top</span>
</nav>
<div class="abs copy">All Rights Reserved ™ ©2010-2015 Tavipor.</div>
<div class="abs foot-dots"><span></span><span></span><span></span><span style="background:#e0584a"></span></div>
<div class="abs legal" style="left:666px">Terms and Rules</div>
<div class="abs legal" style="left:737px">Forum</div>

</body>
</html>
```